Cover für den Roman Hanna betritt die Leinwand
Zielgruppe
Autorin einer belletristischen Erzählung über die Kunst der Moderne. Das Buch richtet sich an Leser die sich für Moderne Kunst interessieren.
Aufgabenstellung
Gesucht wird ein sehr zeitgemäßes und auffallendes Design, auch gerne mit einer starken Hintergrundfarbe. Der Leser soll auf den ersten Blick erkennen können, dass es hier um Kunst geht (Odo Marquet, Drosanow, Veluzzi Ferrant, etc). Bitte unbedingt alle Lizenzrechte abklären und keine Originalwerke verwenden.
Eine Idee wäre einen Bezug zu "Hanna und der Barakleon" herzustellen. (Vielzitiertes Thema in der Kunstgeschichte, Hanna schlägt dem Feldherrn Barakleon den Kopf ab und befreit ihr Volk.)
Das Design sollte aber trotzdem nett und nicht gruselig sein.
Ganz wichtig keine nackte Hanna. Sie ist stark und emanzipiert sich!
Text auf der Vorderseite:
Wiebke Talhammer
Hanna betritt die Leinwand
Erzählung über die Kunst der Moderne
Text auf der Rückseite:
kurze Inhaltsangabe
Das Cover soll für ein Taschenbuch als auch ein e-book funktionieren

```html
<!DOCTYPE html>
<html lang="de">
<head>
<meta charset="utf-8">
<title>Hanna betritt die Leinwand – Umschlag</title>
<link rel="stylesheet" href="https://fonts.googleapis.com/css2?family=Fondamento&family=Cinzel:wght@500;600&family=Alike&family=Noto+Serif:wght@400;700&family=Arimo&display=swap">
<style>
  :root {
    --ink-dark: #2f2e22;
    --band-green: rgba(222, 228, 186, 0.82);
    --box-green: rgba(214, 222, 170, 0.86);
    --title-orange: #e07a22;
    --title-green: #8ea43e;
    --title-green-edge: #e9efc9;
    --subtitle-white: #fbf7ee;
    --art-cream: #efe3c4;
    --art-orange: #e0742a;
    --art-red: #b8322a;
    --art-dark: #2a211c;
    --art-blue: #2f6f9a;
    --art-teal: #4aa0a8;
    --art-yellow: #f2c14e;
  }
  * { box-sizing: border-box; margin: 0; padding: 0; }
  html, body { width: 1200px; height: 830px; overflow: hidden; background: #ffffff; }

  .cover {
    position: relative;
    width: 1200px;
    height: 830px;
    overflow: hidden;
  }

  .cover-artwork {
    position: absolute;
    inset: 0;
    background:
      radial-gradient(ellipse 260px 200px at 330px 230px, var(--art-cream) 0%, rgba(239,227,196,0) 70%),
      radial-gradient(ellipse 300px 260px at 900px 150px, var(--art-yellow) 0%, rgba(242,193,78,0) 70%),
      radial-gradient(ellipse 260px 300px at 120px 120px, var(--art-orange) 0%, rgba(224,116,42,0) 75%),
      radial-gradient(ellipse 280px 220px at 560px 680px, var(--art-red) 0%, rgba(184,50,42,0) 75%),
      radial-gradient(ellipse 320px 260px at 1120px 420px, var(--art-blue) 0%, rgba(47,111,154,0) 75%),
      radial-gradient(ellipse 240px 200px at 1050px 760px, var(--art-teal) 0%, rgba(74,160,168,0) 75%),
      radial-gradient(ellipse 260px 260px at 60px 600px, var(--art-dark) 0%, rgba(42,33,28,0) 75%),
      linear-gradient(135deg, #c9652c 0%, #e8d3a6 40%, #b9502e 65%, #3d6f8a 100%);
  }

  .spine {
    position: absolute;
    left: 558px;
    top: 0;
    width: 93px;
    height: 830px;
    background: var(--band-green);
  }
  .spine-text {
    position: absolute;
    left: 50%;
    transform: translateX(-50%);
    writing-mode: vertical-rl;
    font-family: "Noto Serif", serif;
    font-size: 26px;
    color: var(--ink-dark);
    white-space: nowrap;
  }
  .spine-title { top: 36px; }
  .spine-author { top: 572px; }

  .front-author-band {
    position: absolute;
    left: 651px;
    top: 33px;
    width: 549px;
    height: 60px;
    background: var(--band-green);
  }
  .front-author {
    position: absolute;
    left: 0;
    width: 420px;
    top: 8px;
    text-align: center;
    font-family: "Noto Serif", serif;
    font-weight: 700;
    font-size: 32px;
    color: var(--ink-dark);
    letter-spacing: 0.5px;
  }

  .front-title {
    position: absolute;
    left: 720px;
    top: 340px;
    width: 480px;
    text-align: center;
  }
  .title-name {
    display: block;
    font-family: "Fondamento", cursive;
    font-size: 140px;
    line-height: 1;
    color: var(--title-orange);
    margin-left: 40px;
  }
  .title-verb {
    display: block;
    margin-top: -28px;
    font-family: "Cinzel", serif;
    font-weight: 600;
    font-size: 52px;
    letter-spacing: 3px;
    color: var(--title-green);
    -webkit-text-stroke: 1.5px var(--title-green-edge);
  }
  .title-object {
    display: block;
    margin-top: 12px;
    margin-right: 90px;
    font-family: "Cinzel", serif;
    font-weight: 600;
    font-size: 58px;
    color: var(--title-green);
    -webkit-text-stroke: 1.5px var(--title-green-edge);
  }

  .front-subtitle {
    position: absolute;
    left: 690px;
    top: 688px;
    width: 490px;
    text-align: center;
    font-family: "Alike", serif;
    font-size: 36px;
    line-height: 1.2;
    color: var(--subtitle-white);
  }

  .back-blurb {
    position: absolute;
    left: 68px;
    top: 301px;
    width: 410px;
    height: 367px;
    padding: 16px 12px 10px 12px;
    background: var(--box-green);
    font-family: "Arimo", sans-serif;
    font-size: 24px;
    line-height: 42px;
    color: #111111;
    overflow: hidden;
  }
  .blurb-text { word-break: break-all; }
  .blurb-dots {
    white-space: nowrap;
    overflow: hidden;
    letter-spacing: 1px;
  }
</style>
</head>
<body>
<div class="cover">
  <div class="cover-artwork" role="img" aria-label="Großflächige, farbkräftige Malerei in Orange, Rot, Creme und Blau über den gesamten Umschlag"></div>

  <section class="back-blurb">
    <p class="blurb-text">KlappentextKlappentextKlappentextKlappentextKlappentextKlappentextKlappentextKlappentextKlappentextKlappentext.....................</p>
    <p class="blurb-dots">..........................................................................</p>
    <p class="blurb-dots">..........................................................................</p>
    <p class="blurb-dots">..........................................................................</p>
    <p class="blurb-dots">...................................</p>
  </section>

  <div class="spine">
    <span class="spine-text spine-title">Hanna betritt die Leinwand</span>
    <span class="spine-text spine-author">Wiebke Talhammer</span>
  </div>

  <div class="front-author-band">
    <p class="front-author">Wiebke Talhammer</p>
  </div>

  <h1 class="front-title">
    <span class="title-name">Hanna</span>
    <span class="title-verb">BETRITT DIE</span>
    <span class="title-object">Leinwand</span>
  </h1>

  <p class="front-subtitle">Erzählung über die<br>Kunst der Moderne</p>
</div>
</body>
</html>
```